holloway paving service

Needs to have phone number 0418259730 and email markholloway@brightmail.com.au.
ABN 62318470915
name mark holloway

For all your concreting solutions
Excavation
Exposed & colour concrete
House & shed slabs
Driveways
Landing & steps

Contact Information for Business Card

ph 0418259730
email markholloway@brightmail.com.au.
ABN 62318470915
name mark holloway

```html
<!DOCTYPE html>
<html lang="en">
<head>
<meta charset="utf-8">
<title>Holloway Paving Service – Business Card</title>
<link href="https://fonts.googleapis.com/css2?family=Lato:wght@400;700&display=swap" rel="stylesheet">
<style>
  :root {
    --bg: #3b3532;
    --card: #0d0d0d;
    --orange: #f26b21;
    --grey: #8a8a8a;
    --light: #d9d9d9;
    --white: #f2f2f2;
    --rule: #3a3a3a;
  }
  * { box-sizing: border-box; margin: 0; padding: 0; }
  html, body { width: 1200px; height: 844px; overflow: hidden; }
  body {
    background: var(--bg);
    font-family: "Lato", Arial, sans-serif;
    position: relative;
  }
  .card {
    position: absolute;
    top: 267px;
    width: 540px;
    height: 310px;
    background: var(--card);
    box-shadow: 0 10px 30px rgba(0,0,0,.45);
  }
  .card--front { left: 40px; }
  .card--back { left: 620px; }

  /* Front */
  .front-brand {
    position: absolute;
    left: 36px; top: 118px;
    width: 190px;
    display: flex; align-items: center; gap: 10px;
  }
  .brand-square { width: 22px; height: 22px; background: var(--orange); flex: none; }
  .front-brand .brand-name {
    color: var(--orange);
    font-weight: 700; font-size: 15px; letter-spacing: .5px; line-height: 1.2;
    text-transform: uppercase;
  }
  .front-divider {
    position: absolute; left: 250px; top: 78px;
    width: 1px; height: 150px; background: var(--rule);
  }
  .contact { position: absolute; left: 275px; top: 90px; color: var(--light); }
  .contact__name { font-size: 19px; font-weight: 700; text-transform: uppercase; letter-spacing: .5px; margin-bottom: 8px; }
  .contact__name .first { color: var(--orange); }
  .contact__name .last { color: var(--grey); }
  .contact__line { font-size: 15px; margin-bottom: 6px; display: flex; align-items: center; gap: 8px; }
  .contact__line svg { width: 12px; height: 12px; fill: var(--orange); flex: none; }

  /* Back */
  .back-brand {
    position: absolute; left: 60px; top: 70px;
    display: flex; align-items: center; gap: 16px;
  }
  .back-brand .brand-square { width: 40px; height: 40px; background: var(--white); }
  .back-brand .brand-name {
    color: var(--white); font-size: 24px; font-weight: 400; letter-spacing: 1px;
    text-transform: uppercase; padding-left: 16px; border-left: 1px solid var(--grey); line-height: 56px;
  }
  .back-rule {
    position: absolute; left: 40px; right: 40px; top: 160px;
    height: 1px; background: var(--rule);
  }
  .services { position: absolute; left: 0; right: 0; top: 180px; text-align: center; color: var(--light); }
  .services__title { font-weight: 700; font-size: 15px; color: var(--white); text-transform: uppercase; letter-spacing: .5px; margin-bottom: 8px; }
  .services__list { font-size: 14px; line-height: 1.55; }
</style>
</head>
<body>
  <section class="card card--front">
    <div class="front-brand">
      <span class="brand-square"></span>
      <span class="brand-name">Holloway Paving Service</span>
    </div>
    <div class="front-divider"></div>
    <div class="contact">
      <p class="contact__name"><span class="first">Mark</span> <span class="last">Holloway</span></p>
      <p class="contact__line">ABN 62318470915</p>
      <p class="contact__line">
        <svg viewBox="0 0 12 12" aria-hidden="true"><path d="M2.5 1h2l1 3-1.5 1a6.5 6.5 0 0 0 3 3l1-1.5 3 1v2c0 .6-.4 1-1 1A10 10 0 0 1 1.5 2c0-.6.4-1 1-1z"/></svg>
        0418259730
      </p>
      <p class="contact__line">
        <svg viewBox="0 0 12 12" aria-hidden="true"><path d="M1 2.5h10v7H1z M1 2.5l5 4 5-4" /></svg>
        markholloway@brightmail.com.au
      </p>
    </div>
  </section>

  <section class="card card--back">
    <div class="back-brand">
      <span class="brand-square"></span>
      <span class="brand-name">Holloway Paving Service</span>
    </div>
    <div class="back-rule"></div>
    <div class="services">
      <p class="services__title">For all your concreting solutions</p>
      <p class="services__list">Excavation &nbsp;| &nbsp;Exposed &amp; colour concrete<br>House &amp; shed slabs &nbsp;| Driveways &nbsp;| Landing &amp; steps</p>
    </div>
  </section>
</body>
</html>
```